Broschüre für Hausmeisterservice
Zielgruppe
Unser Hausmeisterservice bietet zuverlässige und professionelle Dienstleistungen rund um die Immobilie. Dazu gehören unter anderem die Pflege und Wartung von Gebäuden, kleinere Reparaturen, Reinigungsarbeiten, Gartenpflege sowie Winterdienst. Unser Ziel ist es, Eigentümern, Hausverwaltungen und Unternehmen einen sorgenfreien Rundum-Service zu bieten, damit ihre Immobilien stets gepflegt und funktionstüchtig sind. Unsere Zielgruppe sind somit Hausverwaltungen, Eigentümergemeinschaften, Firmen und Privatpersonen, die Wert auf eine gepflegte Immobilie legen und einen zuverlässigen Partner suchen.
Aufgabenstellung
Corporate Design und Kommunikation:
Freundlich, vertrauenswürdig und professionell wirken
Klare, verständliche Sprache verwenden
Visuelle Elemente, die Sauberkeit, Ordnung und gepflegte Immobilien ausstrahlen
Call-to-Action:
Klare Aufforderungen zur Kontaktaufnahme, Angebotserstellung oder Terminvereinbarung.

```html
<!DOCTYPE html>
<html lang="de">
<head>
<meta charset="utf-8">
<title>Hauswerk Brandt – Broschüre</title>
<link href="https://fonts.googleapis.com/css2?family=Poppins:ital,wght@0,400;0,500;0,600;0,700;1,400;1,600;1,700&display=swap" rel="stylesheet">
<style>
  :root{
    --bg:#a3a3a3;
    --coral:#ee6352;
    --coral-deep:#c44c3f;
    --ink:#1b1b1b;
    --text:#3a3a3a;
    --paper:#ffffff;
    --paper-grey:#dcdcdc;
    --card:#efecea;
  }
  *{box-sizing:border-box;margin:0;padding:0}
  html,body{width:1200px;height:1200px;overflow:hidden;background:var(--bg);font-family:"Poppins",sans-serif;color:var(--ink)}
  .canvas{position:relative;width:1200px;height:1200px}
  .spread{position:absolute;left:28px;top:300px;display:flex;height:600px;box-shadow:0 18px 40px rgba(0,0,0,.25)}
  .panel{width:276px;height:600px;position:relative;overflow:hidden}
  .section-title{display:flex;align-items:center;gap:12px;font-weight:700;font-size:26px;color:var(--ink)}
  .section-title::before{content:"";width:7px;height:30px;background:var(--coral)}

  /* Über uns */
  .panel--about{background:linear-gradient(160deg,var(--paper) 0%,var(--paper-grey) 100%);padding:44px 26px}
  .about-lead{margin-top:30px;font-size:10px;font-weight:600}
  .about-text{margin-top:6px;font-size:7.5px;line-height:1.45;color:var(--text)}
  .signature{margin-top:18px;width:90px;height:34px;background:linear-gradient(90deg,rgba(0,0,0,.12),rgba(0,0,0,.04));border-radius:4px}
  .about-illustration{position:absolute;left:30px;bottom:0;width:216px;height:300px;border-radius:110px 110px 0 0;background:linear-gradient(180deg,#f0a24a 0%,#e4633c 45%,#2d6e78 80%,#22384a 100%)}

  /* Kennzahlen */
  .panel--stats{background:linear-gradient(135deg,var(--coral) 0%,var(--coral-deep) 100%);color:#fff;padding:40px 30px;display:flex;flex-direction:column;gap:26px}
  .stat-value{font-weight:700;font-size:70px;line-height:1;letter-spacing:-1px}
  .stat-label{font-size:17px;font-weight:400;margin-top:4px}

  /* Leistungen */
  .panel--services{background:var(--paper);padding:44px 20px}
  .service-list{margin-top:26px;display:flex;flex-direction:column;gap:16px}
  .service{display:flex;gap:10px;background:var(--card);padding:10px;border-radius:2px;height:140px}
  .service-photo{flex:0 0 104px;height:100%;border-radius:1px}
  .service-photo--street{background:linear-gradient(160deg,#4f6b3e,#8a9a8a 60%,#2a3a5a)}
  .service-photo--repair{background:linear-gradient(160deg,#2f3a33,#3f7a5a 55%,#b07a3a)}
  .service-photo--glass{background:linear-gradient(160deg,#d8dadc,#6d7275 60%,#2b2f33)}
  .service h3{font-size:10.5px;font-weight:600;line-height:1.2}
  .service p{margin-top:5px;font-size:7.5px;line-height:1.45;color:var(--text)}

  /* Titelseite */
  .cover{position:absolute;left:896px;top:300px;width:276px;height:600px;background:var(--paper);overflow:hidden;box-shadow:0 18px 40px rgba(0,0,0,.25)}
  .cover-badge{position:absolute;left:50px;top:-2px;width:176px;height:170px;border:2px solid var(--coral);border-top:none;border-radius:0 0 88px 88px;background:var(--paper);display:flex;flex-direction:column;align-items:center;justify-content:center;gap:6px;box-shadow:0 8px 14px rgba(0,0,0,.12)}
  .brand{display:flex;align-items:center;gap:6px;font-weight:700;font-size:12px;color:var(--ink)}
  .brand-dot{width:12px;height:12px;border-radius:50%;background:var(--coral)}
  .brand-claim{font-size:5.5px;font-weight:500;letter-spacing:.3px;color:var(--text)}
  .cover-headline{position:absolute;top:210px;left:16px;right:16px;text-align:center;font-size:17px;line-height:1.3;font-style:italic;font-weight:400}
  .cover-headline strong{font-weight:700}
  .cover-sub{position:absolute;top:302px;left:20px;right:20px;text-align:center;font-size:8.5px;font-style:italic;color:var(--text)}
  .cover-cta{position:absolute;top:350px;left:42px;width:192px;height:34px;border-radius:8px;background:#f08275;color:#fff;font-size:10px;font-style:italic;display:flex;align-items:center;justify-content:center;box-shadow:0 6px 12px rgba(238,99,82,.3)}
  .cover-photo{position:absolute;left:0;bottom:0;width:276px;height:180px;background:linear-gradient(180deg,#fafafa 0%,#cdbda8 35%,#7a5a40 60%,#2c3236 100%)}
</style>
</head>
<body>
<main class="canvas">
  <section class="spread">
    <article class="panel panel--about">
      <h2 class="section-title">Über Uns</h2>
      <p class="about-lead">Die Geschichte hinter HAUSWERK BRANDT</p>
      <p class="about-text">HAUSWERK BRANDT bietet seit 6 Jahren erstklassige Reinigungs- und Instandhaltungsdienstleistungen an. Mit einem Schwerpunkt auf Vielseitigkeit hat das Team beeindruckende Ergebnisse erzielt, indem es Kunden bei der Bewältigung verschiedenster Aufgaben unterstützt.</p>
      <div class="signature" role="img" aria-label="Handschriftliche Unterschrift des Inhabers"></div>
      <div class="about-illustration" role="img" aria-label="Illustration eines Hausmeisters mit Putzeimer, Besen und Reinigungsmitteln"></div>
    </article>

    <article class="panel panel--stats">
      <div class="stat"><div class="stat-value">6</div><div class="stat-label">Jahre Erfahrung</div></div>
      <div class="stat"><div class="stat-value">700+</div><div class="stat-label">Zufriedene Kunden</div></div>
      <div class="stat"><div class="stat-value">08+</div><div class="stat-label">Preisgekrönt</div></div>
      <div class="stat"><div class="stat-value">98%</div><div class="stat-label">Kundenzufriedenheit</div></div>
    </article>

    <article class="panel panel--services">
      <h2 class="section-title">Leistungen</h2>
      <div class="service-list">
        <div class="service">
          <div class="service-photo service-photo--street" role="img" aria-label="Foto: Reinigung einer Straße mit Hochdruckreiniger"></div>
          <div><h3>Straßenreinigung</h3><p>Unser erfahrenes Team reinigt gründlich Straßen und sorgt für ein gepflegtes Erscheinungsbild. Wir entfernen Schmutz, Laub und Unkraut, um die Straße sicher und ansprechend zu machen.</p></div>
        </div>
        <div class="service">
          <div class="service-photo service-photo--repair" role="img" aria-label="Foto: Werkzeuge und Akkuschrauber für Reparaturen"></div>
          <div><h3>Grillreparatur / Haushaltssachen</h3><p>Unsere Experten für Grillreparaturen kümmern sich um alle Ihre Bedürfnisse, reparieren Starter, ersetzen Batterien und stehen mit unserer Fachkompetenz zur Verfügung.</p></div>
        </div>
        <div class="service">
          <div class="service-photo service-photo--glass" role="img" aria-label="Foto: Glasfassade eines Gebäudes"></div>
          <div><h3>Glasreinigung</h3><p>Wir reinigen Fenster, Fassaden und Glasdächer streifenfrei und sorgen für klare Sicht.</p></div>
        </div>
      </div>
    </article>
  </section>

  <section class="cover">
    <div class="cover-badge">
      <div class="brand"><span class="brand-dot"></span>HAUSWERK BRANDT</div>
      <div class="brand-claim">UNSERE ARBEIT. FÜR IHRE ZUFRIEDENHEIT</div>
    </div>
    <h1 class="cover-headline">Ihr <strong>zuverlässiger Partner</strong> für <strong>alle Reinigungs -und Wartungsdienstleistungen</strong></h1>
    <p class="cover-sub">Professionelle Reinigung, Gartenpflege, Reparaturarbeiten und mehr</p>
    <div class="cover-cta">www.hauswerk-brandt.de</div>
    <div class="cover-photo" role="img" aria-label="Foto: modernes Wohnhaus mit Holzfassade und Balkon"></div>
  </section>
</main>
</body>
</html>
```